PSD Designs needed to give to my Developer

Hello, I need PSD files to give to my programmer for the creation of my new website. The website is for KORVA lane, a new clothing company based in Chicago, IL. We sell womens, mens and kids fashion. We specialize in jackets, outerwear and sweaters, but we sell clothing from every category, I have someone working on the logo, so I can't include it for reference. However, I have included 2 reference sites as well as a PDF of how the 2 reference sites could be merged together. The main company color should be blue (hence the name KORVA lane), and the overall feel of the site should be FUN. It should communicate: This is where you want to shop if you want a FUN, HAPPY experience. I need the Home Page file designed very quickly. Whoever is awarded this job will immediately continue working with me to design the other 8 pages. I will pay for all pages. The amount I am offering is for this one page only, and I will pay you additional to design all other 8 pages. Thank you for your time and I will be picking the best design so that we can immediately build a great relationship and work through the rest of the project.

Industry/Entity Type

Apparel Store

Number of Pages Required

1 page

Font styles to use
Sans Serif

Colors
33a6d7
0492cd
ffffff

Requirements
Must have
• I have included all notes in the project description so please check there. My project must communicate: Fun and Happy Design. Even tho I have chosen a few variations of blue below, I still want the designer to incorporate other colors as necessary to acheive the desired look.
Should not have
• It should have a boring, childish feel

```html
<!DOCTYPE html>
<html lang="en">
<head>
<meta charset="utf-8">
<title>KORVA lane — Home</title>
<link href="https://fonts.googleapis.com/css2?family=Montserrat:wght@400;500;600;700&family=Oswald:wght@600;700&display=swap" rel="stylesheet">
<style>
:root{
  --blue:#33a6d7;
  --blue-deep:#0492cd;
  --blue-rim:#8cc7e0;
  --white:#ffffff;
  --ink:#333333;
  --hero-bg:#f6f5f3;
  --tri:#d7e9f0;
  --jacket:#b9895a;
}
*{box-sizing:border-box;margin:0;padding:0}
html,body{width:990px;height:1200px;overflow:hidden;background:var(--white)}
body{position:relative;font-family:'Montserrat',sans-serif;color:var(--ink)}
.promo-bar{position:absolute;top:0;left:0;width:990px;height:48px;background:var(--blue);color:var(--white)}
.promo-bar__text{position:absolute;left:70px;top:14px;font-size:15px;font-weight:500}
.stylist-login{position:absolute;left:802px;top:10px;width:116px;height:28px;border:1.5px solid var(--white);border-radius:2px;display:flex;align-items:center;justify-content:center;gap:7px;font-size:12px;font-weight:500}
.main-nav{position:absolute;top:48px;left:0;width:990px;height:72px;background:var(--white)}
.main-nav__links{position:absolute;left:70px;top:29px;display:flex;gap:27px;font-size:13px;letter-spacing:.2px;list-style:none}
.brand{position:absolute;right:72px;top:18px;font-size:30px;font-weight:700;color:var(--blue-deep);white-space:nowrap}
.hero{position:absolute;top:120px;left:0;width:990px;height:411px;background:var(--hero-bg);overflow:hidden}
.hero__art{position:absolute;left:0;top:0}
.hero__title{position:absolute;right:352px;top:107px;text-align:right;font-family:'Oswald',sans-serif;font-weight:700;color:var(--white);font-size:56px;line-height:62px;letter-spacing:1px}
.hero__sub{position:absolute;left:411px;top:237px;color:var(--white);font-size:13px;font-weight:600}
.hero__cta{position:absolute;left:598px;top:269px;width:96px;height:96px;border-radius:50%;display:flex;align-items:center;justify-content:center;color:var(--white);font-size:11px;font-weight:700}
.slider-arrow{position:absolute;top:194px;width:25px;height:25px;border-radius:50%;background:#2b2b2b;display:flex;align-items:center;justify-content:center}
.slider-arrow svg{display:block}
.tiles{position:absolute;top:531px;left:0;width:990px;height:318px;display:flex}
.tile{position:relative;width:330px;height:318px;overflow:hidden}
.tile__label{position:absolute;font-family:'Oswald',sans-serif;font-weight:700;color:var(--white);line-height:1}
.tile--story{background:linear-gradient(180deg,#3b3b3b,#8a7d72 55%,#bfb2a4)}
.tile--shop{background:linear-gradient(90deg,#3a8fc0 0%,#4a7fa0 45%,#c9c3ba 60%,#d9d4cc)}
.tile--movement{background:linear-gradient(180deg,#f2c532,#e9b52a 60%,#3d3220)}
.newsletter{position:absolute;top:849px;left:0;width:990px;height:351px;background:linear-gradient(180deg,#1f3a44 0%,#1e2224 40%,#17191a);color:var(--white);text-align:center}
.newsletter__title{position:absolute;top:45px;width:100%;font-size:30px;font-weight:500;letter-spacing:7px}
.newsletter__lead{position:absolute;top:90px;left:320px;width:350px;font-size:11.5px;line-height:16px}
.signup{position:absolute;top:131px;left:250px;display:flex;gap:16px}
.signup__input{width:342px;height:42px;background:var(--white);border-radius:2px;text-align:left;padding:14px 19px;font-size:10.5px;font-style:italic;color:#9a9a9a}
.signup__button{width:134px;height:42px;background:var(--blue);display:flex;align-items:center;justify-content:center;font-size:15px;font-weight:500;letter-spacing:.5px}
.social{position:absolute;top:193px;left:403px;display:flex;gap:9px}
.social span{width:30px;height:30px;border-radius:50%;background:var(--blue)}
.footer-links{position:absolute;top:252px;left:253px;display:flex;gap:29px;font-size:12px;font-weight:500;list-style:none}
.copyright{position:absolute;top:285px;width:100%;font-size:12px;font-weight:500}
</style>
</head>
<body>
<header class="promo-bar">
  <p class="promo-bar__text">Pop-up your own KORVA Boulevard for ONLY $99</p>
  <div class="stylist-login">
    <svg width="9" height="11" viewBox="0 0 9 11"><rect x="0" y="4.5" width="9" height="6.5" rx="1" fill="#fff"/><path d="M2 4.5V3a2.5 2.5 0 0 1 5 0v1.5" fill="none" stroke="#fff" stroke-width="1.4"/></svg>
    Stylist Login
  </div>
</header>

<nav class="main-nav">
  <ul class="main-nav__links">
    <li>HOME</li><li>GET TO KNOW US</li><li>WHY KORVA?</li><li>HOST A POP-UP</li><li>BECOME A STYLIST</li>
  </ul>
  <div class="brand">KORVA lane</div>
</nav>

<section class="hero">
  <svg class="hero__art" width="990" height="411" viewBox="0 0 990 411">
    <defs>
      <radialGradient id="modelGlow" cx="50%" cy="55%" r="55%">
        <stop offset="0" stop-color="var(--jacket)" stop-opacity="0.75"/>
        <stop offset="0.6" stop-color="#c9a27a" stop-opacity="0.45"/>
        <stop offset="1" stop-color="var(--hero-bg)" stop-opacity="0"/>
      </radialGradient>
    </defs>
    <polygon points="0,30 25,15 90,186 0,176" fill="var(--tri)"/>
    <polygon points="944,176 990,265 990,320 852,308" fill="var(--tri)"/>
    <polygon points="909,340 928,411 838,411" fill="var(--tri)"/>
    <g role="img" aria-label="Smiling man in tan suede bomber jacket and white trousers">
      <ellipse cx="330" cy="260" rx="140" ry="240" fill="url(#modelGlow)"/>
    </g>
    <circle cx="534" cy="204" r="170" fill="var(--blue-rim)"/>
    <circle cx="530" cy="204" r="168" fill="var(--blue)"/>
    <circle cx="646" cy="317" r="52" fill="var(--white)"/>
    <circle cx="646" cy="317" r="48" fill="var(--blue-deep)"/>
  </svg>
  <div class="hero__title">LIMITED<br>INVENTORY</div>
  <p class="hero__sub">that's only available for ONE week!</p>
  <div class="hero__cta">SHOP NOW &gt;</div>
  <div class="slider-arrow" style="left:25px"><svg width="8" height="10" viewBox="0 0 8 10"><path d="M6 1 2 5l4 4" fill="none" stroke="#fff" stroke-width="1.5"/></svg></div>
  <div class="slider-arrow" style="left:940px"><svg width="8" height="10" viewBox="0 0 8 10"><path d="M2 1l4 4-4 4" fill="none" stroke="#fff" stroke-width="1.5"/></svg></div>
</section>

<section class="tiles">
  <div class="tile tile--story" role="img" aria-label="Two laughing friends in hats sitting together">
    <span class="tile__label" style="left:70px;top:42px;font-size:44px">OUR STORY</span>
  </div>
  <div class="tile tile--shop" role="img" aria-label="Couple posing in denim and a light blazer">
    <span class="tile__label" style="left:123px;top:230px;font-size:40px">SHOP</span>
  </div>
  <div class="tile tile--movement" role="img" aria-label="Boy in knit beanie against a yellow wall">
    <span class="tile__label" style="right:70px;top:160px;font-size:42px;text-align:right;line-height:46px">BE HAPPIER,<br>JOIN THE<br>MOVEMENT</span>
  </div>
</section>

<footer class="newsletter" role="img" aria-label="Dim background of a woman relaxing in summer clothes">
  <h2 class="newsletter__title">NEWSLETTER SIGN UP</h2>
  <p class="newsletter__lead">Lorem ipsum dolor sit amet, consectetur adipisicing elit,sed do eiusmod ut labore et dolore</p>
  <div class="signup">
    <div class="signup__input">Enter your email...</div>
    <div class="signup__button">SUBSCRIBE</div>
  </div>
  <div class="social" aria-label="Social links"><span></span><span></span><span></span><span></span><span></span></div>
  <ul class="footer-links"><li>Home</li><li>Get To Know Us</li><li>Why Korva?</li><li>Host A Pop-up</li><li>Become A Stylist</li></ul>
  <p class="copyright">Copyright © 2018. KORVA lane. All rights reserved.</p>
</footer>
</body>
</html>
```